New Joomla Website for Marquee Hire Co

We need a web design for our new Marquee Hire Co here in New Zealand called Breezy Canopies.
We rather like the retro look, as it fit very well with the current trends in weddings that is a more of a retro look (and we had our logo designed to reflect that!). The 50's and 60's wedding styles are really making a comeback. We would like to communicate to that market effectively.

The Home page should have a slider image with space for a headline on it. It is a visual product we have (but we are selling that dream of a perfect wedding/party/event).

Our competition here have a really nice site that you could look at - www.plovanto.co.nz

The other pages would have space for a picture, and then a blurb under each element related to it.
We will have a FAQ, Gallery, Hire and Contact us pages - we will add them as we go along.

From a technical perspective, we are using Joomla 2.5 and upwards.

Any questions - let me know. I look forward seeing the designs!

Target Market(s)

Couples looking for a wedding marquee, birthday parties, Corporate events

Industry/Entity Type

Wedding

Requirements
Must have
• 1. Preferably done in Joomla. I will also look at Wordpress site.
2. It has to have a retro look and feel.
3. It has to use my brand new logo (included)

```html
<!DOCTYPE html>
<html lang="en">
<head>
<meta charset="utf-8">
<title>Breezy Canopies – Marquee Hire New Zealand</title>
<link rel="stylesheet" href="https://fonts.googleapis.com/css2?family=Lobster&family=Lobster+Two:ital,wght@1,700&family=Questrial&family=PT+Sans:ital@1&family=Tinos&display=swap">
<style>
  :root {
    --cream: #fdf7dc;
    --white: #ffffff;
    --teal: #44aab6;
    --teal-text: #3fa9b8;
    --brown: #55311a;
    --brown-dark: #3e2410;
    --text: #4a2e12;
    --sky-light: #9fd8ee;
    --sky-top: #8fb8f0;
    --sky-deep: #1f34c9;
  }
  html, body { margin: 0; padding: 0; overflow: hidden; background: var(--white); }
  .canvas { position: relative; width: 1029px; height: 1200px; overflow: hidden; background: var(--white); font-family: "Questrial", sans-serif; color: var(--text); }
  .backdrop { position: absolute; inset: 0; }
  .abs { position: absolute; }

  /* brand */
  .brand { left: 150px; top: 150px; display: flex; align-items: center; gap: 12px; }
  .brand-dot { width: 58px; height: 58px; border-radius: 50%; background: var(--teal); }
  .brand-name { font-family: "Lobster", cursive; font-size: 34px; color: var(--brown); white-space: nowrap; }

  /* navigation */
  .main-nav { left: 468px; top: 152px; transform: rotate(-14deg); transform-origin: left bottom; display: flex; align-items: center; gap: 20px; font-family: "Lobster Two", cursive; font-style: italic; font-weight: 700; font-size: 20px; color: var(--brown); }
  .main-nav a { color: inherit; text-decoration: none; }
  .nav-dot { width: 5px; height: 5px; border-radius: 50%; background: var(--brown); }

  /* promo */
  .promo { left: 95px; top: 274px; width: 254px; height: 198px; background: linear-gradient(180deg, #c9def0 0%, #e9efe9 35%, #8a9f78 60%, #4f7a2c 100%); }
  .promo-title { position: absolute; top: 48px; width: 100%; text-align: center; font-family: "Lobster", cursive; font-size: 23px; color: var(--white); text-shadow: 0 1px 3px rgba(0,0,0,.45); }
  .promo-value { position: absolute; top: 82px; width: 100%; text-align: center; font-family: "Lobster", cursive; font-size: 32px; color: var(--white); text-shadow: 0 1px 3px rgba(0,0,0,.45); }
  .promo-plus { position: absolute; right: 10px; bottom: 4px; color: var(--white); font-size: 20px; font-weight: bold; }

  /* feature cards */
  .card { width: 254px; }
  .card-head { position: relative; display: block; }
  .card-icon { position: absolute; left: 22px; bottom: 10px; width: 56px; height: 40px; background: var(--white); border-radius: 22px 22px 2px 2px; }
  .card-title { position: absolute; left: 98px; bottom: 12px; font-family: "Lobster", cursive; font-size: 26px; color: var(--white); }
  .zigzag { height: 5px; background: linear-gradient(135deg, var(--teal) 50%, transparent 50%) 0 0 / 6px 6px repeat-x, linear-gradient(225deg, var(--teal) 50%, transparent 50%) 0 0 / 6px 6px repeat-x; background-color: var(--white); }
  .card-body { background: var(--white); padding: 8px 17px 6px 21px; height: 180px; box-sizing: border-box; position: relative; }
  .card-sub { margin: 0 0 9px; font-size: 14px; line-height: 20px; color: var(--teal-text); text-transform: uppercase; font-weight: normal; }
  .card-text { margin: 0; font-size: 14.5px; line-height: 20px; text-align: justify; color: var(--text); }
  .more-link { position: absolute; right: 10px; bottom: 4px; font-family: "Lobster", cursive; font-size: 14px; color: var(--teal-text); text-decoration: none; }
  .more-link b { font-family: sans-serif; font-size: 18px; margin-left: 4px; }

  /* hero slider */
  .hero { left: 95px; top: 506px; width: 843px; height: 315px; background: linear-gradient(170deg, var(--sky-top) 0%, #b6d4f6 40%, #6f86e4 62%, var(--sky-deep) 100%); }
  .hero-headline { position: absolute; left: 22px; top: 183px; width: 293px; height: 41px; box-sizing: border-box; padding-left: 13px; background: rgba(255,255,255,.82); font-family: "Lobster Two", cursive; font-style: italic; font-weight: 700; font-size: 27px; line-height: 41px; color: var(--brown); margin: 0; }
  .hero-headline span { text-decoration: underline; text-underline-offset: 3px; }
  .hero-lead { position: absolute; left: 22px; top: 232px; width: 379px; height: 61px; box-sizing: border-box; padding: 9px 14px; background: rgba(230,230,255,.82); font-family: "PT Sans", sans-serif; font-style: italic; font-size: 17px; line-height: 21px; color: var(--brown-dark); margin: 0; }

  /* ribbon */
  .ribbon { left: 0; top: 850px; }

  /* footer */
  .footer-col { top: 940px; width: 250px; font-family: "Tinos", serif; font-size: 13px; line-height: 15.5px; color: var(--text); }
  .footer-col h3 { margin: 0 0 4px; display: inline-block; font-family: "Lobster", cursive; font-weight: normal; font-size: 19px; color: var(--sky-light); border-bottom: 1px dotted var(--teal); padding-bottom: 1px; }
  .footer-col p { margin: 0 0 15.5px; }
  .tweet-dot { display: inline-block; width: 16px; height: 16px; border-radius: 50%; background: var(--sky-light); margin-left: 12px; vertical-align: -1px; }

  .to-top { left: 490px; top: 1159px; width: 67px; height: 41px; }
  .to-top span { position: absolute; left: 0; right: 0; top: 12px; text-align: center; font-family: "Lobster", cursive; font-size: 18px; color: var(--white); }
  .copyright { left: 695px; top: 1175px; font-family: Arial, sans-serif; font-size: 9.5px; color: var(--teal-text); }
</style>
</head>
<body>
<div class="canvas">
  <svg class="backdrop" width="1029" height="1200" aria-hidden="true">
    <polygon points="0,270 1029,13 1029,935 0,1180" fill="var(--cream)"/>
  </svg>

  <header>
    <div class="abs brand"><span class="brand-dot"></span><span class="brand-name">Breezy Canopies</span></div>
    <nav class="abs main-nav">
      <a href="#">Faq</a><span class="nav-dot"></span>
      <a href="#">Gallery</a><span class="nav-dot"></span>
      <a href="#">Hire</a><span class="nav-dot"></span>
      <a href="#">Contact Us</a>
    </nav>
  </header>

  <main>
    <a class="abs promo" href="#" role="img" aria-label="Photo of an open white marquee with sofas on a lawn by the sea">
      <span class="promo-title">Awesome discount!</span>
      <span class="promo-value">-20%</span>
      <span class="promo-plus">+</span>
    </a>

    <article class="abs card" style="left:385px; top:178px;">
      <div class="card-head">
        <svg width="254" height="103" style="display:block"><polygon points="0,47 254,0 254,103 0,103" fill="var(--teal)"/></svg>
        <span class="card-icon" role="img" aria-label="Tent icon"></span>
        <h2 class="card-title" style="margin:0">Nullam digni</h2>
      </div>
      <div class="zigzag"></div>
      <div class="card-body" style="height:186px">
        <h3 class="card-sub">Tincidunt tempus.<br>Suspendisse ut nisl sapien</h3>
        <p class="card-text">Lorem ipsum dolor sit amet, consectetur adipiscing elit. Donec molestie in nisi non consectetur. Nullam dignissim cursus urna ac tempor. Fusce eget arcu nec ipsum</p>
        <a class="more-link" href="#">More info<b>+</b></a>
      </div>
    </article>

    <article class="abs card" style="left:684px; top:101px;">
      <div class="card-head">
        <svg width="254" height="182" style="display:block"><polygon points="0,62 254,0 254,182 0,182" fill="var(--teal)"/></svg>
        <span class="card-icon" role="img" aria-label="Tent icon"></span>
        <h2 class="card-title" style="margin:0">Nullam digni</h2>
      </div>
      <div class="zigzag"></div>
      <div class="card-body" style="height:186px">
        <h3 class="card-sub">Tincidunt tempus.<br>Suspendisse ut nisl sapien</h3>
        <p class="card-text">Lorem ipsum dolor sit amet, consectetur adipiscing elit. Donec molestie in nisi non consectetur. Nullam dignissim cursus urna ac tempor. Fusce eget arcu nec ipsum</p>
        <a class="more-link" href="#">More info<b>+</b></a>
      </div>
    </article>

    <section class="abs hero" role="img" aria-label="Slider photo of a blue circus-style marquee roof with flags against the sky">
      <h1 class="hero-headline">Contact Us for a <span>Quote</span></h1>
      <p class="hero-lead">Have you ever dreamed of getting married by the sea or in the mountains?</p>
    </section>
  </main>

  <svg class="abs ribbon" width="1029" height="60" aria-hidden="true">
    <polygon points="88,12 131,12 131,42 75,42" fill="var(--brown)"/>
    <polygon points="941,12 975,12 963,42 907,42" fill="var(--brown)"/>
    <polygon points="99,5 939,5 939,36 540,36 520,52 500,36 99,36" fill="var(--brown)"/>
    <polygon points="99,36 131,36 131,42" fill="var(--brown-dark)"/>
    <polygon points="939,36 907,36 907,42" fill="var(--brown-dark)"/>
  </svg>

  <footer>
    <div class="abs footer-col" style="left:117px;">
      <h3>Contact</h3>
      <p>12 Kauri Lane,<br>Tahuna, New Zealand</p>
      <p>+64 21 555 0142<br>hello@breezycanopies.co.nz</p>
    </div>
    <div class="abs footer-col" style="left:398px;">
      <h3>About</h3>
      <p>We are a dedicated team working to take part in your dreamed event project. Breezy Canopies is helping people build memories. Special occasions is worth celebrating.</p>
    </div>
    <div class="abs footer-col" style="left:678px;">
      <h3>Recent Tweets</h3><span class="tweet-dot"></span>
      <p>2 hours ago : @BreezyCanopies Thank you for your service, it was fabulous!</p>
      <p>A day ago : New discount in Markees!</p>
    </div>

    <a class="abs to-top" href="#">
      <svg width="67" height="41" aria-hidden="true"><polygon points="33.5,0 67,41 0,41" fill="var(--brown)"/></svg>
      <span>Up</span>
    </a>
    <div class="abs copyright">© 2013 Breezy Canopies All Rights Reserved</div>
  </footer>
</div>
</body>
</html>
```